Blow Dry Bar Business Cards

These cards must be eye catching and modern.
You must be willing to work fast and make changes.

Winner will be offered other projects

Files 1 THIS IS THE STYLE CARDS I AM INTRESTED IN!!!
Please be creative, I am paying for my own eye catching design. I need files to be nexa press ready.

COLORS THAT ARE PAINTED INSIDE MY SHOP:
- - - http://www.quorvelpaint.example/en/explore-colors/painter/color-selector.html?colors=4007-3C

- - - http://www.brandivex.example/color/paint-colors/hidden-corridor-d58-2

I want the business cards sleek and modern if you use the logo please correct imperfections. I added the part that says Blow Dry Bar (see website).
Do not be afraid to separate the blow dryer from the name to make the cards look like the file with the pink elephant.

SHOULD INCLUDE
*Blow Dryer (we are a blow dry bar not a salon we do not cut or color so do not include sheers of any kind)
*BUSINESS NAME: Simply Swept Upward - Blow Dry Bar (PLEASE SEE MY WEBSITE)
* Website: SIMPLYSWEPTUPWARD.EXAMPLE
*Phone number (555) 014-2763
Updates

Nexa press said it can be submitted in JPG

http://www.brandivex.example/color/paint-colors/hidden-corridor-d58-2 http://www.quorvelpaint.example/en/explore-colors/painter/color-selector.html?colors=4007-3C ^^^^ These links will take you to the color paint that is painted inside my shop.

Target Market(s)

AGES 18 - 55 WOMEN
HIGH END MARKET

Industry/Entity Type

Salon

Requirements
Must have
• SEE COLOR EXAMPLE FILE
BLOW DRYER
UNIQUE
I LIKE THE CARD WITH THE PINK ELEPHANT THE BEST
Nice to have
• BE AS CREATIVE AND MODERN AS POSSIBLE DO NOT COPY ANY OF THE CARDS BELOW.
Should not have
• SCISSORS
PINK

```html
<!DOCTYPE html>
<html lang="en">
<head>
<meta charset="utf-8">
<title>Simply Swept Upward – Business Cards</title>
<link rel="stylesheet" href="https://fonts.googleapis.com/css2?family=Questrial&family=Didact+Gothic&display=swap">
<style>
  :root {
    --backdrop: #e4e4e4;
    --card: #38373f;
    --mark: #141317;
    --ink: #ffffff;
    --ink-soft: #e9e9ee;
  }
  html, body {
    margin: 0;
    padding: 0;
    overflow: hidden;
  }
  body {
    width: 1200px;
    height: 1200px;
    background: var(--backdrop);
    position: relative;
    font-family: "Questrial", sans-serif;
  }
  .card {
    position: absolute;
    left: 258px;
    width: 682px;
    height: 384px;
    background: var(--card);
    color: var(--ink);
  }
  .card--front { top: 172px; }
  .card--back { top: 626px; }

  .front-brand {
    position: absolute;
    left: 72px;
    top: 168px;
    white-space: nowrap;
  }
  .front-brand__name {
    margin: 0;
    font-family: "Questrial", sans-serif;
    font-weight: 400;
    font-size: 46px;
    line-height: 1;
    color: var(--ink);
  }
  .front-brand__tagline {
    margin: 8px 0 0 14px;
    font-family: "Questrial", sans-serif;
    font-size: 24px;
    letter-spacing: 1px;
    color: var(--ink);
  }
  .front-mark {
    position: absolute;
    left: 548px;
    top: 118px;
  }

  .back-brand {
    position: absolute;
    right: 376px;
    top: 256px;
    text-align: right;
    white-space: nowrap;
  }
  .back-brand__name {
    margin: 0;
    font-family: "Questrial", sans-serif;
    font-size: 18px;
    line-height: 1.2;
    color: var(--ink);
  }
  .back-brand__tagline {
    margin: 6px 0 0;
    font-family: "Didact Gothic", sans-serif;
    font-size: 14px;
    color: var(--ink-soft);
  }
  .back-mark {
    position: absolute;
    left: 322px;
    top: 284px;
  }
  .back-contact {
    position: absolute;
    left: 424px;
    top: 256px;
    font-family: "Didact Gothic", sans-serif;
    font-size: 15px;
    line-height: 1.55;
    letter-spacing: 0.4px;
    color: var(--ink-soft);
    white-space: nowrap;
  }
  .back-contact p { margin: 0; }
</style>
</head>
<body>
  <section class="card card--front" aria-label="Business card front">
    <div class="front-brand">
      <h1 class="front-brand__name">Simply Swept Upward</h1>
      <p class="front-brand__tagline">premier blow dry bar</p>
    </div>
    <svg class="front-mark" width="112" height="112" viewBox="0 0 112 112" role="img" aria-label="Brand mark">
      <circle cx="56" cy="56" r="56" fill="var(--mark)"/>
    </svg>
  </section>

  <section class="card card--back" aria-label="Business card back">
    <div class="back-brand">
      <p class="back-brand__name">Simply Swept Upward</p>
      <p class="back-brand__tagline">blow dry bar</p>
    </div>
    <svg class="back-mark" width="36" height="36" viewBox="0 0 36 36" role="img" aria-label="Brand mark">
      <circle cx="18" cy="18" r="18" fill="var(--mark)"/>
    </svg>
    <div class="back-contact">
      <p class="back-contact__web">SIMPLYSWEPTUPWARD.EXAMPLE</p>
      <p class="back-contact__phone">P: (555) 014-2763</p>
    </div>
  </section>
</body>
</html>
```